Online homewares store needs a web design

We need a web design for a new high-end online homewares store. We are starting small with only 5 major categories.

Rugs
Bathe
Dine
Decorative
Sleep

This is just for design. No coding needed.

Please make high-end, sophisticated and minimal.

I have included some pictures to give you an idea of the products. I would like to showcase some of the pictures on the web page.

The website will be using an e-commerce function.

I have included the logo studio nine harbors.

I like this website
http://mapleandquarrylane.example/

or

borvanest.example.au

Simple but effective - not too busy

Project Deadline Extended
Reason: I would like to extend my deadline to give designers more time to do quality work - as requested!! Thanks.

Target Market(s)

Females in the age bracket of 25-45

Males who are very house proud 25-45

Industry/Entity Type

Store

Requirements
Must have
• Upmarket

```html
<!DOCTYPE html>
<html lang="en">
<head>
<meta charset="utf-8">
<title>studio nine harbors — Homewares</title>
<link rel="stylesheet" href="https://fonts.googleapis.com/css2?family=Raleway:wght@300;400&family=Open+Sans:wght@400;600;700&family=Bitter:ital,wght@1,700&display=swap">
<style>
:root{
  --pink:#e5168f;
  --black:#000;
  --ink:#222;
  --dark-card:#2f2f2f;
  --muted:#8d8f93;
  --band:#e2e4e7;
  --page:#e9eaec;
  --white:#fff;
  --line:#c9cbce;
}
*{box-sizing:border-box;margin:0;padding:0}
html,body{width:683px;height:1200px;overflow:hidden}
body{background:var(--page);font-family:'Open Sans',sans-serif;color:var(--ink);position:relative}
.abs{position:absolute}

/* top bar */
.topbar{left:0;top:0;width:683px;height:36px;background:var(--black)}
.brand{left:44px;top:3px;font-family:'Raleway',sans-serif;font-weight:300;font-size:23px;color:var(--white);letter-spacing:-.2px}
.util{top:12px;font-size:8px;color:#ccc;display:flex;align-items:center;gap:4px}
.util svg{width:11px;height:11px}
.login{left:522px;top:10px;width:85px;height:15px;background:#3a3a3a;border-radius:2px;font-size:7.5px;color:#fff;text-align:center;line-height:15px}
.login em{font-style:normal;color:#888}
.search{left:615px;top:6px;width:22px;height:22px;border-radius:50%;background:var(--pink)}

/* nav */
.nav{left:0;top:36px;width:683px;height:28px;background:var(--white)}
.nav a{position:absolute;top:9px;font-size:8.5px;color:#444;text-decoration:none}
.nav-sep{position:absolute;top:8px;width:1px;height:12px;background:#ddd}
.home-tab{left:63px;top:36px;width:41px;height:36px;background:var(--pink);clip-path:polygon(0 0,100% 0,100% 100%,50% 85%,0 100%);color:#fff;font-size:8.5px;font-weight:700;text-align:center;padding-top:9px}
.cartbox{left:550px;top:42px;width:87px;height:17px;border:1px solid #ddd;border-radius:2px;font-size:7.5px;color:#888;display:flex;align-items:center;padding-left:6px;gap:4px}
.cartbox b{color:var(--pink);font-weight:600}

/* hero */
.hero{left:0;top:64px;width:683px;height:283px;background:linear-gradient(135deg,#b84a5e,#d98a3a 25%,#5f8f4e 45%,#4a6fa8 65%,#c45b86 85%,#7a5a9a)}
.hero-copy{left:370px;top:150px;font-family:'Bitter',serif;font-style:italic;font-weight:700;font-size:18.5px;line-height:23px;color:#fff}
.hero-btn{left:370px;top:228px;width:70px;height:20px;background:#222;color:#fff;font-family:'Bitter',serif;font-style:italic;font-weight:700;font-size:11.5px;text-align:center;line-height:20px}

/* category tabs */
.cats{left:0;top:347px;width:683px;height:71px;background:var(--band)}
.cats-rule{left:63px;top:347px;width:557px;height:3px;background:var(--black)}
.cats-active{left:176px;top:347px;width:109px;height:3px;background:var(--pink)}
.cat{top:358px;width:111px;text-align:center;border-right:1px solid #d3d5d8;height:32px}
.cat h3{font-weight:600;font-size:11px;color:#7b7d81}
.cat p{font-size:7.5px;color:#a3a5a9}
.cat.active h3{color:var(--pink)}
.cat.active p{color:#444}

/* featured */
.featured{left:0;top:418px;width:683px;height:188px;background:var(--black)}
.sec-title{font-size:13px;color:var(--white)}
.title-rule{left:170px;top:441px;width:420px;height:1px;background:#777}
.arrow{top:433px;width:19px;height:19px;border-radius:50%;background:#444}
.fcard{top:466px;width:131px;height:120px;background:#fff;border-radius:3px}
.fimg{position:absolute;left:5px;top:5px;width:121px;height:80px}
.name{position:absolute;left:7px;font-size:8.5px;color:#333}
.itemno{position:absolute;left:7px;font-size:7px;color:#999}
.price{position:absolute;width:44px;height:44px;border-radius:50%;background:#2a2a2a;border:2px solid #fff;box-shadow:0 0 0 1px #2a2a2a;color:#fff;font-size:9.5px;font-weight:600;display:flex;flex-direction:column;align-items:center;justify-content:center;line-height:11px}
.price s{font-size:7px;font-weight:400;text-decoration:none}
.price.pink{background:var(--pink);box-shadow:0 0 0 1px var(--pink)}
.price.light{background:#fff;color:#333;border:2px solid #333;box-shadow:none}
.hot{position:absolute;right:0;top:0;width:30px;height:30px;background:var(--pink);clip-path:polygon(0 0,100% 0,100% 100%)}

/* latest */
.latest-title{left:44px;top:625px;font-size:13px;color:#222}
.dots{left:165px;top:634px;width:473px;border-top:2px dotted #c4c6c9}
.lcard{width:122px;height:114px;background:var(--dark-card);border-radius:3px}
.limg{position:absolute;left:5px;top:5px;width:112px;height:80px}
.lcard .name{color:#fff;top:86px}
.lcard .itemno{color:#bbb;top:98px}
.offer{left:490px;top:650px;width:148px;height:114px;background:#fff;border:1px solid #ccc}
.offer-img{position:absolute;left:4px;top:4px;width:138px;height:70px;background:linear-gradient(120deg,#8a2f3a,#c79a5a 40%,#4d6b8a 70%,#b05a6a)}
.offer-txt{position:absolute;left:6px;top:73px;font-size:12px;font-weight:600;color:#222;line-height:14px}
.offer-big{position:absolute;left:6px;top:86px;font-size:21px;font-weight:600;color:var(--pink);line-height:24px}
.offer-big b{color:#111;font-weight:600}
.offer-big small{font-size:10px;color:var(--pink);font-weight:400}
.wear{left:490px;top:782px;width:148px;height:114px;background:linear-gradient(90deg,#5c5d61,#8a8b8f)}
.wear-img{position:absolute;right:0;top:0;width:72px;height:114px;background:linear-gradient(180deg,#d9b48a,#e86a8a 60%,#d4557a)}
.wear h4{position:absolute;left:10px;top:10px;font-size:12px;font-weight:600;color:#fff;line-height:13px}
.wear p{position:absolute;left:10px;top:38px;width:60px;font-size:6.5px;color:#ddd;line-height:9px}
.wear .buy{position:absolute;left:12px;top:78px;width:34px;height:12px;background:#f0a500;border-radius:2px;font-size:6.5px;color:#222;text-align:center;line-height:12px}

/* why shop */
.why{left:45px;top:918px;width:593px;height:38px;border-top:1px solid var(--pink);border-bottom:1px solid var(--pink)}
.why-label{left:45px;top:918px;width:107px;height:38px;background:var(--black);color:#fff;font-size:9px;line-height:38px;text-align:center}
.perk{top:926px;display:flex;align-items:center;gap:5px;font-size:8px;font-weight:400;color:#222;line-height:10px}
.perk svg{width:18px;height:18px;flex:none}

/* contact strip */
.contact{left:45px;top:976px;width:593px;height:66px;background:var(--black)}
.contact-in{left:51px;top:982px;width:581px;height:54px;background:#fff}
.csep{top:986px;width:1px;height:46px;background:#ddd}
.clabel{font-size:8.5px;color:#333}
.social{top:1009px;width:13px;height:13px}
.phone{left:215px;top:1006px;font-size:14px;color:var(--pink);font-weight:400}
.email{left:354px;top:1009px;width:219px;height:17px;border:1px solid #ccc;font-size:6.5px;font-style:italic;color:#999;padding-left:6px;line-height:15px}
.submit{left:573px;top:1009px;width:47px;height:17px;background:var(--pink);color:#fff;font-size:9px;font-weight:700;text-align:center;line-height:17px}

/* footer */
.footer{left:45px;top:1062px;width:593px;height:122px;background:#fff;border:2px solid #222}
.fhead{font-size:9.5px;color:#222;border-left:2px solid var(--pink);padding-left:4px;line-height:10px}
.flist{list-style:none;font-size:7.5px;color:#444;line-height:14px}
.fbrand{left:488px;top:1092px;width:148px;height:24px;background:var(--black);font-family:'Raleway',sans-serif;font-weight:300;font-size:16px;color:#fff;line-height:23px;padding-left:4px}
.accept{left:489px;top:1131px;font-size:8px;font-style:italic;font-weight:700;color:#222}
.pay{top:1128px;width:22px;height:15px;border-radius:2px}
.copy{left:45px;top:1163px;width:593px;border-top:1px solid #ddd;text-align:center;font-size:8px;color:#333;padding-top:3px}
</style>
</head>
<body>

<!-- Header -->
<div class="abs topbar"></div>
<div class="abs brand">studio nine harbors</div>
<div class="abs util" style="left:330px"><svg viewBox="0 0 12 12"><circle cx="6" cy="3.5" r="2.5" fill="#e5168f"/><path d="M1 12c0-4 10-4 10 0z" fill="#e5168f"/></svg>My Account</div>
<div class="abs util" style="left:393px"><svg viewBox="0 0 12 12" fill="none" stroke="#e5168f" stroke-width="1.3"><path d="M0 1h2l2 7h6l1.5-5H3"/><circle cx="5" cy="10.5" r="1"/><circle cx="9" cy="10.5" r="1"/></svg>Shopping Cart</div>
<div class="abs util" style="left:467px"><svg viewBox="0 0 12 12"><circle cx="6" cy="6" r="5.5" fill="#e5168f"/><path d="M3 6h5M6 4l2 2-2 2" stroke="#fff" fill="none"/></svg>Checkout</div>
<div class="abs login">Login <em>-- or --</em> Register</div>
<div class="abs search"><svg viewBox="0 0 22 22" width="22" height="22"><circle cx="10" cy="10" r="4" fill="none" stroke="#fff" stroke-width="2"/><path d="M13 13l3.5 3.5" stroke="#fff" stroke-width="2.2"/></svg></div>

<nav class="abs nav">
  <a style="left:112px">Rugs</a><span class="nav-sep" style="left:146px"></span>
  <a style="left:160px">Bathe</a><span class="nav-sep" style="left:197px"></span>
  <a style="left:212px">Dine</a><span class="nav-sep" style="left:243px"></span>
  <a style="left:259px">Decorative</a><span class="nav-sep" style="left:315px"></span>
  <a style="left:330px">Sleep</a><span class="nav-sep" style="left:366px"></span>
  <a style="left:381px">Contact Us</a>
</nav>
<div class="abs home-tab">Home</div>
<div class="abs cartbox"><svg width="10" height="9" viewBox="0 0 12 12" fill="none" stroke="#e5168f" stroke-width="1.3"><path d="M0 1h2l2 7h6l1.5-5H3"/></svg>Cart <b>$0.00</b><span style="margin-left:18px;font-size:6px">▾</span></div>

<!-- Hero -->
<div class="abs hero" role="img" aria-label="Child's bare feet standing on a colourful felt-ball rug"></div>
<div class="abs hero-copy">Lorem ipsum dolor sit amet,<br>consectetuer adipiscing elit,<br>sed diam nonummy nibh</div>
<div class="abs hero-btn">VIEW ALL</div>

<!-- Category tabs -->
<div class="abs cats"></div>
<div class="abs cats-rule"></div>
<div class="abs cats-active"></div>
<div class="abs cat" style="left:64px"><h3>Rugs</h3><p>Lorem Ipsum Sit Dolor</p></div>
<div class="abs cat active" style="left:175px"><h3>Bathe</h3><p>Lorem Ipsum Sit Dolor</p></div>
<div class="abs cat" style="left:286px"><h3>Dine</h3><p>Lorem Ipsum Sit Dolor</p></div>
<div class="abs cat" style="left:397px"><h3>Decorative</h3><p>Lorem Ipsum Sit Dolor</p></div>
<div class="abs cat" style="left:508px;border:none"><h3>Sleep</h3><p>Lorem Ipsum Sit Dolor</p></div>

<!-- Featured -->
<div class="abs featured"></div>
<div class="abs sec-title" style="left:44px;top:433px">Featured Products</div>
<div class="abs title-rule"></div>
<div class="abs arrow" style="left:594px"><svg viewBox="0 0 19 19" width="19" height="19"><path d="M11 6l-3 3.5 3 3.5" stroke="#fff" stroke-width="1.5" fill="none"/></svg></div>
<div class="abs arrow" style="left:619px"><svg viewBox="0 0 19 19" width="19" height="19"><path d="M8 6l3 3.5-3 3.5" stroke="#fff" stroke-width="1.5" fill="none"/></svg></div>

<div class="abs fcard" style="left:45px">
  <div class="fimg" role="img" aria-label="Living room with cream patterned rug and sofa" style="background:linear-gradient(160deg,#b59a7c,#e8e2d6 55%,#cfc3ae)"></div>
  <div class="hot"></div>
  <div class="name" style="top:90px">Rugs</div><div class="itemno" style="top:104px">Item No. : 1254</div>
  <div class="price pink" style="left:81px;top:69px">$190.00</div>
</div>
<div class="abs fcard" style="left:199px">
  <div class="fimg" role="img" aria-label="Stacked patterned cushions and throws" style="background:linear-gradient(150deg,#6b2b1e,#b84a2e 45%,#7a8a3a)"></div>
  <div class="name" style="top:90px">Rugs New</div><div class="itemno" style="top:104px">Item No. : 1254</div>
  <div class="price" style="left:81px;top:69px">$190.00</div>
</div>
<div class="abs fcard" style="left:353px">
  <div class="fimg" role="img" aria-label="Red and black decorative vases with flowers" style="background:linear-gradient(160deg,#c6c9d8,#e9b5c8 40%,#c23030 70%,#333)"></div>
  <div class="name" style="top:90px">Dine</div><div class="itemno" style="top:104px">Item No. : 1254</div>
  <div class="price" style="left:81px;top:69px"><s>$230.00</s>$190.00</div>
</div>
<div class="abs fcard" style="left:507px">
  <div class="fimg" role="img" aria-label="Folded black and white striped towels" style="background:linear-gradient(170deg,#cfc8bd,#2b2b2b 45%,#e6e2dc 60%,#222)"></div>
  <div class="name" style="top:90px;font-size:7.5px">Bathe</div><div class="itemno" style="top:104px">Item No. : 1254</div>
  <div class="price" style="left:81px;top:69px">$190.00</div>
</div>

<!-- Latest -->
<div class="abs latest-title">Latest Products</div>
<div class="abs dots"></div>

<div class="abs lcard" style="left:45px;top:650px">
  <div class="limg" role="img" aria-label="Black and white table runner with potted plant" style="background:linear-gradient(160deg,#6b3a2a,#2a1a14 50%,#dedede 65%,#222)"></div>
  <div class="name">Rugs New</div><div class="itemno">Item No. : 1254</div>
  <div class="price pink" style="left:73px;top:68px"><s>$230.00</s>$190.00</div>
</div>
<div class="abs lcard" style="left:190px;top:650px">
  <div class="limg" role="img" aria-label="White sofa with printed cushion" style="background:linear-gradient(160deg,#e9e7e2,#fafafa 50%,#9a9a9a)"></div>
  <div class="name">Decorative</div><div class="itemno">Item No. : 1254</div>
  <div class="price light" style="left:73px;top:68px">$190.00</div>
</div>
<div class="abs lcard" style="left:335px;top:650px">
  <div class="limg" role="img" aria-label="Elegant cream dining room" style="background:linear-gradient(160deg,#d8cbb5,#efe7d8 50%,#a8967a)"></div>
  <div class="name">Decorative</div><div class="itemno">Item No. : 1254</div>
  <div class="price light" style="left:73px;top:68px">$190.00</div>
</div>
<div class="abs offer">
  <div class="offer-img" role="img" aria-label="Colourful knitted throw with tag"></div>
  <div class="offer-txt">Special</div>
  <div class="offer-big">OFFER<b>15%</b> <small>off</small></div>
</div>

<div class="abs lcard" style="left:45px;top:782px">
  <div class="limg" role="img" aria-label="Round natural rug with colourful felt edging on a dark floor" style="background:linear-gradient(150deg,#4a3a32,#b98a6a 45%,#c9a07a 60%,#3a302c)"></div>
  <div class="name">Rugs</div><div class="itemno">Item No. : 1254</div>
  <div class="price light" style="left:73px;top:68px">$190.00</div>
</div>
<div class="abs lcard" style="left:190px;top:782px">
  <div class="limg" role="img" aria-label="Dining table with linen tablecloth" style="background:linear-gradient(160deg,#6a5a48,#d8c6a6 50%,#a08a68)"></div>
  <div class="name">Dine</div><div class="itemno">Item No. : 1254</div>
  <div class="price light" style="left:73px;top:68px">$190.00</div>
</div>
<div class="abs lcard" style="left:335px;top:782px">
  <div class="limg" role="img" aria-label="Felt-ball garland on white wall" style="background:linear-gradient(160deg,#f0ece8,#e9c4cf 50%,#d5d0cc)"></div>
  <div class="name">Decorative</div><div class="itemno">Item No. : 1254</div>
  <div class="price light" style="left:73px;top:68px"><s>$230.00</s>$190.00</div>
</div>
<div class="abs wear">
  <div class="wear-img" role="img" aria-label="Woman in pink t-shirt"></div>
  <h4>Women's<br>Wear</h4>
  <p>Lorem Ipsum is simply dummy te of the prinn...</p>
  <div class="buy">Buy It</div>
</div>

<!-- Why shop -->
<div class="abs why"></div>
<div class="abs why-label">Why Shop With Us?</div>
<div class="abs perk" style="left:162px"><svg viewBox="0 0 18 18"><rect x="3" y="8" width="12" height="9" rx="1" fill="#222"/><path d="M5.5 8V5a3.5 3.5 0 0 1 7 0v3" fill="none" stroke="#222" stroke-width="2"/></svg><span>100% Secure<br>Shopping</span></div>
<div class="abs perk" style="left:250px"><svg viewBox="0 0 18 18"><circle cx="9" cy="9" r="7.5" fill="none" stroke="#222" stroke-width="1.5" stroke-dasharray="2 1"/><path d="M5.5 9l2.5 2.5 4.5-5" fill="none" stroke="#222" stroke-width="1.8"/></svg><span>Money Back<br>Guarantee</span></div>
<div class="abs perk" style="left:342px"><svg viewBox="0 0 20 18" style="width:38px;height:20px"><rect x="0" y="4" width="11" height="9" fill="#222"/><path d="M11 7h4l3 3v3h-7z" fill="#222"/><circle cx="4" cy="14.5" r="2" fill="#222"/><circle cx="14" cy="14.5" r="2" fill="#222"/></svg><span>FREE Delivery<br>over £300*</span></div>
<div class="abs perk" style="left:459px"><svg viewBox="0 0 18 18"><circle cx="9" cy="9" r="7.5" fill="none" stroke="#222" stroke-width="1.5"/><path d="M12 6l-2 5-4 1 2-5z" fill="#222"/></svg><span>Fast<br>Dispatch</span></div>
<div class="abs perk" style="left:538px"><svg viewBox="0 0 18 18"><circle cx="9" cy="9" r="7.5" fill="none" stroke="#222" stroke-width="1.5"/><path d="M5 9l3 3 6-7" fill="none" stroke="#222" stroke-width="2"/></svg><span>Great Customer<br>Feedback</span></div>

<!-- Contact strip -->
<div class="abs contact"></div>
<div class="abs contact-in"></div>
<div class="abs csep" style="left:168px"></div>
<div class="abs csep" style="left:333px"></div>
<div class="abs clabel" style="left:62px;top:991px">FOLLOW US!</div>
<div class="abs social" style="left:62px;background:#3b5998"></div>
<div class="abs social" style="left:80px;background:#3fa9e0"></div>
<div class="abs social" style="left:98px;background:#c8232c"></div>
<div class="abs social" style="left:116px;background:#f08a24"></div>
<div class="abs social" style="left:134px;background:#d33a2c"></div>
<div class="abs clabel" style="left:189px;top:991px">CALL US ON</div>
<svg class="abs" style="left:190px;top:1005px" width="18" height="18" viewBox="0 0 18 18"><path d="M4 1l3 4-2 2c1 2 3 4 5 5l2-2 4 3-2 3C8 16 2 10 1 4z" fill="#222"/></svg>
<div class="abs phone">+123-456-7890</div>
<div class="abs clabel" style="left:354px;top:991px">NEWSLETTER</div>
<div class="abs email">ENTER YOUR EMAIL FOR THE OUR NEWS!</div>
<div class="abs submit">SUBMIT</div>

<!-- Footer -->
<div class="abs footer"></div>
<div class="abs fhead" style="left:63px;top:1080px">Quick Link</div>
<ul class="abs flist" style="left:69px;top:1093px"><li>Home</li><li>Rugs</li><li>Bathe</li><li>Dine</li></ul>
<ul class="abs flist" style="left:108px;top:1093px"><li>Decorative</li><li>Sleep</li><li>Contact Us</li></ul>
<div class="abs fhead" style="left:166px;top:1080px">Customer Service</div>
<ul class="abs flist" style="left:173px;top:1093px"><li>My Account</li><li>Terms and Conditions</li><li>Price Promise</li><li>Returns Policy</li></ul>
<ul class="abs flist" style="left:256px;top:1093px"><li>Delivery</li><li>Customer Service</li><li>Customer Reviews</li><li>Gift Vouchers</li></ul>
<div class="abs fhead" style="left:340px;top:1080px">Popular Products</div>
<ul class="abs flist" style="left:347px;top:1093px"><li>Lorem ipsum</li><li>Lorem ipsum Sit</li><li>Lorem ipsum</li><li>Lorem ipsum Sit</li></ul>
<ul class="abs flist" style="left:410px;top:1093px"><li>Lorem ipsum Sit</li><li>Lorem ipsum</li><li>Lorem ipsum Sit</li><li>Lorem ipsum</li></ul>
<div class="abs fbrand">studio nine harbors</div>
<div class="abs accept">We Accept :</div>
<div class="abs pay" style="left:538px;background:#dfe6f0;border:1px solid #b8c4d6"></div>
<div class="abs pay" style="left:567px;background:#1a3c8c"></div>
<div class="abs pay" style="left:597px;background:#e9e9e9;border:1px solid #ccc"></div>
<div class="abs copy">© 2014 studio nine harbors. All Rights Reserved.</div>

</body>
</html>
```